Coastline Premier Retreats Business Card Design

Design a business card for Coastline Premier Retreats. Look at the website for colors and reference. Card should have logo, name, title, office number, mobile number, email, URL and a tagline like, "Luxury Hotel & Resort Email Marketing" (This might change).

https://www.coastlinepremierretreats.example

The rest I will leave up to your imagination.

Contact Information for Business Card

Logo, name, title, office number, mobile number, email, URL and a tagline like, "Luxury Hotel & Resort Email Marketing" (This might change).

```html
<!DOCTYPE html>
<html lang="en">
<head>
<meta charset="utf-8">
<title>Coastline Premier Retreats – Business Card</title>
<link rel="stylesheet" href="https://fonts.googleapis.com/css2?family=Montserrat:wght@400;500;700;800&display=swap">
<style>
  :root {
    --stage: #2b2b2b;
    --card: #1b1b1b;
    --card-edge: #f07a14;
    --accent: #f07a14;
    --ink: #f2f2f2;
    --ink-soft: #d9d9d9;
    --emboss: #262626;
  }
  * { box-sizing: border-box; margin: 0; padding: 0; }
  html, body {
    width: 1200px; height: 900px; overflow: hidden;
    background: var(--stage);
    font-family: "Montserrat", Arial, sans-serif;
  }
  .stage {
    width: 1200px; height: 900px;
    display: flex; flex-direction: column;
    align-items: center; justify-content: center; gap: 48px;
  }
  .card {
    position: relative;
    width: 700px; height: 400px;
    background: var(--card);
    border-bottom: 5px solid var(--card-edge);
    box-shadow: 0 14px 30px rgba(0,0,0,.45);
  }
  /* Back side */
  .card--back { display: flex; flex-direction: column; align-items: center; justify-content: center; }
  .back__name {
    font-weight: 800; font-size: 40px; letter-spacing: 1px;
    color: var(--emboss); text-transform: uppercase; text-align: center; line-height: 1.15;
  }
  .back__tagline {
    margin-top: 70px; font-size: 20px; font-weight: 500;
    color: var(--accent); letter-spacing: .5px;
  }
  /* Front side */
  .front__brand {
    position: absolute; top: 58px; left: 190px;
    display: flex; align-items: center; gap: 14px;
  }
  .front__brand-mark { width: 20px; height: 20px; background: var(--accent); }
  .front__brand-name {
    font-weight: 800; font-size: 30px; color: var(--ink);
    text-transform: uppercase; letter-spacing: 1px;
  }
  .front__person { position: absolute; left: 70px; top: 200px; text-align: right; width: 270px; }
  .front__person-name {
    font-weight: 800; font-size: 32px; color: var(--accent); text-transform: uppercase; letter-spacing: 1px;
  }
  .front__person-title { font-size: 17px; color: var(--ink-soft); margin-top: 2px; }
  .front__divider {
    position: absolute; left: 370px; top: 150px; width: 1px; height: 120px; background: var(--accent);
  }
  .front__contacts { position: absolute; left: 395px; top: 150px; list-style: none; }
  .front__contacts li {
    display: flex; align-items: center; gap: 10px;
    font-size: 14px; color: var(--ink); line-height: 28px; white-space: nowrap;
  }
  .front__contacts svg { width: 14px; height: 14px; fill: var(--accent); flex: none; }
  .front__address {
    position: absolute; left: 0; right: 0; bottom: 46px;
    text-align: center; font-size: 17px; color: var(--ink);
  }
</style>
</head>
<body>
<main class="stage">
  <section class="card card--back" aria-label="Card back">
    <p class="back__name">Coastline<br>Premier Retreats</p>
    <p class="back__tagline">Luxury Hotel &amp; Resort Email Marketing</p>
  </section>

  <section class="card card--front" aria-label="Card front">
    <div class="front__brand">
      <span class="front__brand-mark"></span>
      <span class="front__brand-name">Coastline Premier Retreats</span>
    </div>

    <div class="front__person">
      <p class="front__person-name">Daniel Reyes</p>
      <p class="front__person-title">CEO/Founder</p>
    </div>

    <div class="front__divider"></div>

    <ul class="front__contacts">
      <li><svg viewBox="0 0 16 16"><path d="M4 1h8a1 1 0 0 1 1 1v12a1 1 0 0 1-1 1H4a1 1 0 0 1-1-1V2a1 1 0 0 1 1-1zm1 2v9h6V3zm3 10a.8.8 0 1 0 0 .01z"/></svg>555.010.2400</li>
      <li><svg viewBox="0 0 16 16"><path d="M3 2l3 1 1 3-2 1a8 8 0 0 0 4 4l1-2 3 1 1 3-2 1C7 14 2 9 2 4z"/></svg>+34 600 000 123</li>
      <li><svg viewBox="0 0 16 16"><path d="M1 4h14v9H1zm1 1v.5l6 4 6-4V5zm0 2v5h12V7l-6 4z"/></svg>info@coastlinepremierretreats.example</li>
      <li><svg viewBox="0 0 16 16"><path d="M8 1a7 7 0 1 0 0 14A7 7 0 0 0 8 1zm0 1.5a5.5 5.5 0 0 1 0 11 5.5 5.5 0 0 1 0-11zM3 8h10v1H3zm4.5-5h1v10h-1z"/></svg>www.coastlinepremierretreats.example</li>
    </ul>

    <p class="front__address">PO Box 45, 88 Harbor Lane, Bayview, CA 90210</p>
  </section>
</main>
</body>
</html>
```